SEO and image area for top of invitation website

We need to add an area on our final category pages for SEO text. Instead of just adding text, we'd like to develop a graphical approach that keeps with our soft, feminine look.

You can view an example of our current final category page at http://www.cardwrenpress.example/invitations/boy-birthday

I've attached an image of what we're thinking it could look like, but you're welcome to alter the design.

The area should be the same width as our site, but can be any height you determine appropriate.

The winner of this project may be approached to develop the additional designs and backgrounds for us as another project. We additionally have several other projects we're interested in doing with the winner.
Updates

We have had a question about the right side of the banner, and what "Free Unlimited Proofs" mean.

About Free Unlimited Proofs:

We are a custom invitation printing company. When a customer orders an invitation from us, they tell us what information we want on the invitation. We then create an electronic sample, or "proof", of what it will look like. We then email it to the customer and they can tell us if they want to make any more changes. We will continue to send them samples, or what we call "proofs", until they are completely satisfied with the way it looks.

We offer Free UNLIMITED Proofs. Compared to our competitors, we are the only one to offer free unlimited proofs.

So, for the right side of this banner, we need an image, or a badge, promoting that we offer free unlimited proofs, and you can include that we are the only ones to do it, if your design has space for that information.

Also, keep in mind, that for other category pages, we may create different images or badges to put in this area - such as for our Low Price Guarantee or to promote a coupon or specific product, for example. So, your design should be able to work with various images on the right side.

Target Market(s)

Our demographic is 100% women, ages 25-60.

Industry/Entity Type

Seo

Requirements
Must have
• The area must have 3 things:
1) Area for the title of the page.
2) Area for SEO text describing the category page.
3) Area for an image. Keep in mind that this image may change for each category page. For this project, you will create an image for our offering of "Free Unlimited Proofs". On other pages, we may display other images we create such as "Low Price Guarantee" or images of certain products we'd like to promote. Just keep this in mind when you're making the design flow.
Nice to have
• Optional: Light design background. We wouldn't mind there being a slight graphical background to this area, to keep it interesting to the eye. Then, for other category pages, we may make additional backgrounds to use in this box area.

```html
<!DOCTYPE html>
<html lang="en">
<head>
<meta charset="utf-8">
<title>Card Wren Press – Boy Birthday Invitations</title>
<link href="https://fonts.googleapis.com/css2?family=Roboto+Slab:wght@400;700&family=Open+Sans:wght@400;700&family=Noticia+Text:wght@400;700&display=swap" rel="stylesheet">
<style>
:root{
  --mauve:#7b6c70;
  --mauve-dark:#6a5c60;
  --gold:#f2cf5b;
  --gold-soft:#f6dc70;
  --cream:#fbf3e6;
  --ink:#555;
  --ink-soft:#777;
  --teal:#2aa6a6;
  --line:#d8d8d8;
  --topbar:#f0f0f0;
  --banner-bg:#dcd8d9;
}
*{box-sizing:border-box;margin:0;padding:0}
html,body{width:1200px;height:960px;overflow:hidden;background:#fff;font-family:"Open Sans",sans-serif;color:var(--ink)}
.page{position:relative;width:1200px;height:960px}

.topbar{position:absolute;left:0;top:0;width:1200px;height:28px;background:var(--topbar);border-bottom:1px solid #ddd;display:flex;justify-content:center;align-items:center;font-size:12px;font-weight:700;color:#555}
.topbar span{padding:0 12px;border-right:1px solid #ddd;display:flex;align-items:center;gap:7px;height:28px}
.topbar span:last-child{border-right:0}
.topbar svg{width:15px;height:13px;fill:#666}

.brand{position:absolute;left:146px;top:44px;display:flex;align-items:center;gap:14px}
.brand-mark{width:58px;height:58px;background:#e9e4e5;border:1px solid #ccc}
.brand-name{font-family:"Roboto Slab",serif;font-size:36px;color:var(--mauve-dark)}
.search{position:absolute;left:486px;top:63px;width:274px;height:45px;border:1px solid #e4e4e4;border-radius:3px;box-shadow:inset 0 1px 3px #eee}
.search-btn{position:absolute;right:6px;top:7px;width:62px;height:28px;background:#c9c9c9;color:#fff;font-family:"Noticia Text",serif;font-weight:700;font-size:12px;border-radius:2px;display:flex;align-items:center;justify-content:center}
.account{position:absolute;left:782px;top:76px;display:flex;gap:15px;font-family:"Noticia Text",serif;font-size:12px;color:#555;align-items:center}
.account svg{width:20px;height:16px;fill:#666}
.account b{font-weight:400;font-size:16px;margin-left:-4px}

.nav{position:absolute;left:143px;top:135px;width:914px;height:46px;border-top:1px solid var(--line);border-bottom:1px solid var(--line);display:flex;align-items:center;padding-left:20px;gap:40px;font-family:"Roboto Slab",serif;font-size:18px;color:#666}

.crumbs{position:absolute;left:143px;top:199px;font-family:"Noticia Text",serif;font-size:12px;color:#666}
.crumbs a{color:var(--teal);text-decoration:none}

.banner{position:absolute;left:189px;top:232px;width:840px;height:171px;background:var(--banner-bg);border-radius:10px;box-shadow:0 0 5px rgba(0,0,0,.35)}
.banner-art{position:absolute;inset:0;border-radius:10px;background:linear-gradient(#e4e1e2,#d5d1d2)}
.banner-title{position:absolute;left:0;top:0;width:317px;height:48px;background:var(--mauve);border-top-left-radius:10px;border-bottom-right-radius:4px;font-family:"Roboto Slab",serif;font-size:29px;color:var(--gold);padding:4px 0 0 14px}
.banner-copy{position:absolute;left:8px;top:60px;width:618px;height:99px;background:var(--mauve);border-radius:5px;color:var(--cream);font-family:"Noticia Text",serif;font-weight:700;font-variant:small-caps;font-size:15px;line-height:23.5px;padding:3px 10px}
.badge{position:absolute;left:646px;top:6px;width:185px;height:153px;border-radius:3px;overflow:hidden}
.badge-head{height:76px;background:var(--gold-soft);color:var(--mauve);font-family:"Noticia Text",serif;font-weight:700;font-variant:small-caps;font-size:23px;line-height:29px;text-align:center;padding-top:8px}
.badge-body{height:77px;background:var(--mauve);color:var(--cream);font-family:"Noticia Text",serif;font-weight:700;font-variant:small-caps;font-size:11px;line-height:13.5px;text-align:center;padding:6px 4px 0}

.sortbar{position:absolute;left:158px;top:434px;display:flex;gap:18px;align-items:baseline;font-family:"Noticia Text",serif;font-size:12px;color:#666}
.sortbar strong{font-weight:400;font-size:15px;color:#555}
.pager{position:absolute;left:866px;top:434px;display:flex;align-items:center;gap:8px;font-family:"Noticia Text",serif;font-size:12px;color:var(--teal)}
.pager .arrow{width:21px;height:21px;border-radius:50%;display:flex;align-items:center;justify-content:center}
.pager .prev{background:#cfcfcf}
.pager .next{background:#5aa9a3}
.pager svg{width:11px;height:11px;fill:#fff}
.pager .current{color:#666}

.filters{position:absolute;left:143px;top:490px;width:228px}
.filter-head{font-family:"Roboto Slab",serif;font-size:16px;color:#666;display:flex;align-items:center;gap:9px;padding-left:10px}
.filter-head::before{content:"";border-left:5px solid #777;border-top:5px solid transparent;border-bottom:5px solid transparent}
.colors{list-style:none;margin:14px 0 0 26px;font-size:12px;color:#777}
.colors li{display:flex;align-items:center;gap:7px;height:19px}
.colors i{width:14px;height:14px;border-radius:50%;border:1px solid #bbb;display:inline-block}
.all-colors{margin:2px 0 0 29px;font-size:12px;color:#777}
.filter-block{border-top:3px solid #ddd;margin-top:9px;height:60px;padding-top:12px}

.grid{position:absolute;left:391px;top:484px;display:grid;grid-template-columns:repeat(3,211px);grid-auto-rows:210px;column-gap:17px;row-gap:20px}
.card{position:relative;border:1px solid #ddd;background:#fff;display:flex;justify-content:center}
.thumb{display:block}
.quick-view{position:absolute;left:50%;bottom:-8px;transform:translateX(-50%);width:91px;height:24px;border-radius:4px;background:linear-gradient(#fbe27c,#f0c93a);border:1px solid #e0b733;font-size:11px;font-weight:700;color:#5a4a3a;display:flex;align-items:center;justify-content:center}
</style>
</head>
<body>
<div class="page">

  <div class="topbar">
    <span><svg viewBox="0 0 16 12"><rect x="0" y="1" width="10" height="8"/><path d="M10 4h3l3 3v2h-6z"/><circle cx="3" cy="10" r="2"/><circle cx="12" cy="10" r="2"/></svg>FREE SHIPPING on orders over $150 - no coupon needed!</span>
    <span><svg viewBox="0 0 16 12"><path d="M1 1h9v6H5l-3 3V7H1z"/><path d="M11 4h4v5h-1v2l-2-2H8V8h3z"/></svg>Live Help</span>
    <span><svg viewBox="0 0 16 12"><path d="M1 4c2-3 12-3 14 0l-1 2-3-1V3H5v2L2 6z"/><rect x="4" y="6" width="8" height="5" rx="1"/></svg>888.555.0142</span>
    <span><svg viewBox="0 0 16 12"><path d="M1 1h7l7 6-5 5-9-7z"/></svg>Become a Designer · Earn Commission</span>
  </div>

  <div class="brand">
    <div class="brand-mark"></div>
    <div class="brand-name">Card Wren Press</div>
  </div>
  <div class="search"><div class="search-btn">search</div></div>
  <div class="account">
    <span>LOGIN</span><span>CREATE ACCOUNT</span>
    <svg viewBox="0 0 20 16"><path d="M0 1h4l3 9h10l2-7H6" fill="none" stroke="#666" stroke-width="2"/><circle cx="8" cy="14" r="1.6"/><circle cx="16" cy="14" r="1.6"/></svg><b>0</b>
  </div>

  <nav class="nav">
    <span>Wedding</span><span>Party</span><span>Baby and Kids</span><span>Holiday</span><span>Graduation</span><span>Business</span><span>Stationery</span>
  </nav>

  <div class="crumbs"><a>Party</a> · <a>Kids Birthday Party Invitations</a> · Boy Birthday Invitations</div>

  <section class="banner">
    <div class="banner-art" role="img" aria-label="Soft grey background with a faint repeating bird pattern"></div>
    <h1 class="banner-title">Boy Birthday Cards</h1>
    <p class="banner-copy">Lorem ipsum dolor sit amet, consectetur adipiscing elit. Mauris sed tortor mauris, et mollis est. Curabitur lobortis neque ut ante venenatis mattis. Nullam nisl erat, suscipit eget viverra in, vestibulum eu mi. Integer elementum arcu magna, id porta odio.</p>
    <aside class="badge">
      <div class="badge-head">Free, Unlimited<br>&amp; Exclusive!</div>
      <div class="badge-body">We offer FREE unlimited proofs, making sure each and every card is just right! Something you won't get anywhere else.</div>
    </aside>
  </section>

  <div class="sortbar"><strong>Sort By:</strong><span>Price</span><span>Name</span><span>Vendor</span></div>
  <div class="pager">
    <span class="arrow prev"><svg viewBox="0 0 12 12"><path d="M11 5H4l3-3-1-1-5 5 5 5 1-1-3-3h7z"/></svg></span>
    <span class="current">1</span><span>2</span><span>3</span><span>4</span><span>5</span><span>6</span><span>7</span><span>8</span><span>9</span>
    <span class="arrow next"><svg viewBox="0 0 12 12"><path d="M1 5h7L5 2l1-1 5 5-5 5-1-1 3-3H1z"/></svg></span>
  </div>

  <aside class="filters">
    <div class="filter-head">Filter By Color</div>
    <ul class="colors">
      <li><i style="background:#222"></i>Black</li>
      <li><i style="background:#4f86e8"></i>Blue</li>
      <li><i style="background:#8a5a3c"></i>Brown</li>
      <li><i style="background:#f2b321"></i>Gold</li>
      <li><i style="background:#7bd67b"></i>Green</li>
      <li><i style="background:#ccc"></i>Grey</li>
      <li><i style="background:#fffff0"></i>Ivory</li>
      <li><i style="background:#f7a055"></i>Orange</li>
      <li><i style="background:#f7c2e6"></i>Pink</li>
      <li><i style="background:#7a1f6e"></i>Purple</li>
      <li><i style="background:#e0443a"></i>Red</li>
      <li><i style="background:#f5f8fa"></i>Silver</li>
      <li><i style="background:#fff"></i>White</li>
      <li><i style="background:#f8ea5e"></i>Yellow</li>
    </ul>
    <div class="all-colors">ALL COLORS</div>
    <div class="filter-block"><div class="filter-head">Filter By Card Size</div></div>
    <div class="filter-block"><div class="filter-head">Filter By # of Photos</div></div>
    <div class="filter-block"><div class="filter-head">Filter By Designer</div></div>
  </aside>

  <main class="grid">
    <div class="card"><svg class="thumb" width="160" height="208" role="img" aria-label="Pirate party invitation with colourful panels and a photo"><rect width="160" height="208" fill="#e84a2f"/><rect y="70" width="80" height="70" fill="#f29c22"/><rect x="80" y="140" width="80" height="68" fill="#7cc142"/><rect y="140" width="80" height="68" fill="#3fa6dd"/><rect width="80" height="70" fill="#6cc04a"/></svg><span class="quick-view">Quick View</span></div>
    <div class="card"><svg class="thumb" width="160" height="208" role="img" aria-label="Birthday invitation with a photo on a green star background"><rect width="160" height="208" fill="#72bf44"/><rect x="20" y="16" width="120" height="80" fill="#8aa36a"/><rect y="98" width="160" height="44" fill="#2d8fd6"/><rect x="10" y="144" width="140" height="54" fill="#f49b25"/></svg><span class="quick-view">Quick View</span></div>
    <div class="card"><svg class="thumb" width="209" height="136" role="img" aria-label="Orange dinosaur birthday invitation"><rect width="209" height="136" fill="#fff"/><ellipse cx="120" cy="70" rx="90" ry="60" fill="#f6a321"/></svg><span class="quick-view">Quick View</span></div>
    <div class="card"><svg class="thumb" width="96" height="208" role="img" aria-label="Bowling party invitation in blue"><rect width="96" height="208" fill="#3ba0de"/><rect x="10" y="70" width="76" height="130" fill="#d6eefa"/></svg><span class="quick-view">Quick View</span></div>
    <div class="card"><svg class="thumb" width="209" height="136" role="img" aria-label="Water slide birthday party invitation"><rect width="209" height="136" fill="#9ccf5a"/><path d="M0 130 L209 40 L209 80 L40 136Z" fill="#f3c41e"/></svg><span class="quick-view">Quick View</span></div>
    <div class="card"><svg class="thumb" width="209" height="136" role="img" aria-label="Outer space birthday invitation with a friendly alien"><rect width="209" height="136" fill="#2aa0e4"/><ellipse cx="60" cy="70" rx="45" ry="28" fill="#7fd35a"/></svg><span class="quick-view">Quick View</span></div>
    <div class="card"><svg class="thumb" width="160" height="208" role="img" aria-label="Bright yellow hang-out party invitation"><rect width="160" height="208" fill="#f6d21a"/></svg></div>
    <div class="card"><svg class="thumb" width="209" height="208" role="img" aria-label="Cream invitation with a red stripe"><rect width="209" height="208" fill="#fbe8b4"/><rect x="20" y="26" width="90" height="8" fill="#c0392b"/></svg></div>
    <div class="card"><svg class="thumb" width="209" height="208" role="img" aria-label="Orange and green guitar themed invitation"><rect width="209" height="208" fill="#f07f23"/><rect x="110" width="99" height="208" fill="#7cc142"/></svg></div>
  </main>

</div>
</body>
</html>
```